Veterinary Pylon

My veterinary clinic is not clearly visible from the street and I want to place a Pylon next to my driveway. I want a modern, elegant straight Design, the Photo shows the sheduled place. One can see the clinic on our Homepage: www.tailbright-vethaus.at
The last pictures are examples for pylones I like

Target Market(s)

the passing cars often miss my entry...I want to show where to turn left

Colors
3276b5
33a6d7
00a990

Requirements
Must have
• High value, simple elegance, size: 250cm (high) x 100cm (width)
Nice to have
• Our Logo, arrow(?)

A special Text is not necessary but this will be an option:

Biegen sie hier ab und wir biegen es wieder hin!
Should not have
• Too much Color, the colors I have chosen are the possible colors but it‘s not necessary to use them.

```html
<!DOCTYPE html>
<html lang="de">
<head>
<meta charset="utf-8">
<title>Tailbright Vethaus – Pylon</title>
<link href="https://fonts.googleapis.com/css2?family=Montserrat:wght@600;700;800;900&display=swap" rel="stylesheet">
<style>
  :root {
    --stage: #6b6b6b;
    --panel: #ffffff;
    --navy: #1b3f8f;
    --cyan: #3bb8dc;
    --halo: #b9deee;
    --mist: #e9ecef;
  }
  * { margin: 0; padding: 0; box-sizing: border-box; }
  html, body {
    width: 1200px; height: 1200px; overflow: hidden;
    background: var(--stage);
    font-family: "Montserrat", sans-serif;
  }
  .pylon {
    position: absolute; left: 380px; top: 50px;
    width: 440px; height: 1100px;
    background: linear-gradient(180deg, var(--panel) 0%, var(--panel) 38%, var(--mist) 70%, var(--panel) 100%);
    overflow: hidden;
  }
  .pylon__texture {
    position: absolute; left: 0; top: 420px; width: 100%; height: 680px;
    background: radial-gradient(ellipse at 30% 60%, rgba(200,205,212,0.45), rgba(255,255,255,0) 70%);
  }
  .logo-art {
    position: absolute; left: 22px; top: 59px; width: 403px; height: 245px;
  }
  .brand-name {
    position: absolute; left: 0; top: 345px; width: 100%;
    text-align: center; color: var(--navy);
    font-weight: 900; font-size: 44px; line-height: 1.02; letter-spacing: 1px;
    text-transform: uppercase;
  }
  .direction-band {
    position: absolute; left: 0; top: 549px; width: 100%; height: 45px;
    background: var(--cyan);
  }
  .direction-sign {
    position: absolute; left: 126px; top: 477px; width: 188px; height: 188px;
  }
  .slogan {
    position: absolute; left: 0; top: 684px; width: 100%;
    text-align: center; color: var(--navy);
    font-weight: 700; font-size: 18.5px; line-height: 28px;
  }
  .contact { position: absolute; left: 60px; top: 762px; color: var(--navy); }
  .contact__row { display: flex; align-items: center; }
  .contact__phone { font-weight: 800; font-size: 29px; letter-spacing: -0.5px; }
  .contact__web { font-weight: 700; font-size: 15.5px; margin-top: 4px; }
  .contact__icon { width: 22px; margin-right: 18px; display: flex; justify-content: center; }
</style>
</head>
<body>
  <div class="pylon">
    <div class="pylon__texture"></div>

    <svg class="logo-art" viewBox="0 0 403 245" role="img" aria-label="Clinic illustration: dog and cat silhouettes inside a heart with a heartbeat line">
      <defs>
        <linearGradient id="artTone" x1="0" y1="0" x2="0" y2="1">
          <stop offset="0" stop-color="#d6edf7"/>
          <stop offset="1" stop-color="#c3cde6"/>
        </linearGradient>
      </defs>
      <rect x="60" y="0" width="290" height="220" rx="20" fill="url(#artTone)"/>
      <path d="M0 232 Q200 205 403 232" stroke="var(--cyan)" stroke-width="4" fill="none"/>
    </svg>

    <div class="brand-name">Tailbright<br>Vethaus</div>

    <div class="direction-band"></div>
    <svg class="direction-sign" viewBox="0 0 188 188" aria-hidden="true">
      <circle cx="94" cy="94" r="94" fill="var(--halo)"/>
      <circle cx="94" cy="94" r="80" fill="var(--navy)"/>
      <path d="M104 150 V90 Q104 72 86 72 H64" stroke="#fff" stroke-width="18" fill="none"/>
      <path d="M72 44 L38 72 L72 100 Z" fill="#fff"/>
    </svg>

    <p class="slogan">BIEGEN SIE HIER AB UND<br>WIR BIEGEN ES WIEDER HIN!</p>

    <div class="contact">
      <div class="contact__row contact__phone">
        <span class="contact__icon">
          <svg width="20" height="22" viewBox="0 0 20 22" aria-hidden="true"><path d="M5 2 L8 7 L6 9 Q8 14 12 16 L14 14 L19 17 L17 21 Q6 20 2 5 Z" fill="none" stroke="var(--navy)" stroke-width="2.2" stroke-linejoin="round"/></svg>
        </span>140-527-316
      </div>
      <div class="contact__row contact__web">
        <span class="contact__icon">
          <svg width="12" height="12" viewBox="0 0 12 12" aria-hidden="true"><circle cx="6" cy="6" r="5" fill="none" stroke="var(--navy)" stroke-width="1.4"/><path d="M1 6 H11 M6 1 Q3 6 6 11 M6 1 Q9 6 6 11" stroke="var(--navy)" stroke-width="1" fill="none"/></svg>
        </span>www.tailbright-vethaus.at
      </div>
    </div>
  </div>
</body>
</html>
```